Velvix app icon design

We are building an Velvix app and would like some good looking icons to replace the boring ones we have created ourselves.

Please see attached screen shots.

The icons toggle "Active/Inactive" where the inactive is shaded out.

Building

```html
<!DOCTYPE html>
<html lang="en">
<head>
<meta charset="utf-8">
<title>Velvix app icons – search states</title>
<link rel="stylesheet" href="https://fonts.googleapis.com/css2?family=Chakra+Petch:wght@600;700&family=Share+Tech+Mono&display=swap">
<style>
  :root{
    --ink:#000;
    --paper:#fff;
    --screen:#f3f3f3;
    --bar-top:#1d5fe6;
    --bar-bottom:#0a3cc4;
    --bar-line:#5aa0ff;
    --home:#3b8cf7;
    --tile:#c9c9c9;
    --cyan:#35e2f3;
    --blue:#0b3cc8;
    --card-line:#b9b9b9;
    --band-top:#eef3f9;
    --band-bottom:#86a4c6;
    --band-line:#1d4fb8;
  }
  *{box-sizing:border-box;margin:0;padding:0}
  html,body{width:1200px;height:651px;overflow:hidden;background:var(--paper)}
  .stage{position:relative;width:955px;height:518px;transform:scale(1.2566);transform-origin:0 0;
    font-family:"Chakra Petch",sans-serif}
  .footer-band{position:absolute;left:0;top:425px;width:955px;height:93px;background:var(--ink)}

  .screen{position:absolute;top:16px;width:292px;height:389px;background:var(--screen)}
  .screen--inactive{left:15px}
  .screen--active{left:327px}
  .screen--single{left:647px}

  .state-tab{position:absolute;top:0;left:50%;transform:translateX(-50%);height:15px;padding:0 16px;
    background:var(--ink);color:var(--paper);font-family:"Share Tech Mono",monospace;font-size:14px;
    line-height:15px;letter-spacing:1px;white-space:nowrap}
  .screen--single .state-tab{width:230px;text-align:center}

  .app-bar{position:absolute;top:17px;left:0;right:0;height:41px;
    background:linear-gradient(var(--bar-top),var(--bar-bottom));border-bottom:2px solid var(--bar-line)}
  .home-btn{position:absolute;left:10px;top:8px;width:63px;height:24px;background:var(--home);
    clip-path:polygon(12px 0,100% 0,100% 100%,12px 100%,0 50%);color:var(--paper);
    font-size:13px;font-weight:700;line-height:24px;padding-left:14px}
  .app-title{position:absolute;left:105px;top:4px;color:var(--paper);font-size:23px;font-weight:700;letter-spacing:1px}

  .categories{position:absolute;top:60px;left:0;right:0;height:66px;display:flex;gap:1px;background:var(--paper)}
  .category{flex:1;background:var(--tile);display:flex;flex-direction:column}
  .category__icon{flex:1;display:flex;align-items:center;justify-content:center;gap:1px;color:var(--cyan)}
  .category__icon svg{width:34px;height:34px}
  .category__label{height:10px;background:var(--cyan);color:var(--paper);font-size:7.5px;font-weight:600;
    text-align:center;line-height:10px;letter-spacing:.4px}
  .is-on .category__icon{color:var(--blue)}
  .is-on .category__label{background:var(--blue)}

  .person{display:block;width:24px;height:28px;border-radius:12px 12px 4px 4px;
    background:linear-gradient(currentColor,currentColor)}
  .person--small{width:16px;height:22px;border-radius:8px 8px 3px 3px;margin-top:6px}

  .search-band{position:absolute;top:128px;left:0;right:0;height:42px;
    background:linear-gradient(var(--band-top),var(--band-bottom));
    border-top:2px solid var(--band-line);border-bottom:2px solid var(--band-line)}
  .search-field{position:absolute;left:8px;right:8px;top:8px;height:22px;background:var(--paper);
    border:1.5px solid #2b5fd0;border-radius:12px}

  .results{position:absolute;top:172px;left:0;right:0;bottom:0;list-style:none}
  .result{position:absolute;left:5px;width:276px;height:46px}
  .result:nth-child(1){top:4px}.result:nth-child(2){top:55px}
  .result:nth-child(3){top:107px}.result:nth-child(4){top:159px}
  .result__icon{position:absolute;left:0;top:0;width:50px;height:46px;background:var(--tile);
    border-top:2px solid var(--cyan);display:flex;align-items:center;justify-content:center;color:var(--cyan)}
  .result__icon svg{width:32px;height:32px}
  .result__card{position:absolute;left:50px;right:0;top:0;height:46px;background:var(--paper);
    border:1px solid var(--card-line);border-radius:8px;padding:8px 0 0 8px;
    color:var(--cyan);font-size:13px;font-weight:700;line-height:15px;letter-spacing:.3px}
  .result--person .result__card{padding-left:11px}
  .screen--active .result__icon{color:var(--blue);border-top-color:var(--blue)}
  .screen--active .result__card,.screen--single .result__card{color:var(--blue)}
</style>
</head>
<body>
<svg width="0" height="0" style="position:absolute" aria-hidden="true">
  <defs>
    <symbol id="icon-house" viewBox="0 0 32 32">
      <path d="M16 4 2 17h4v11h7v-7h6v7h7V17h4L24 10V5h-3v2.5z" fill="currentColor"/>
    </symbol>
    <symbol id="icon-folder" viewBox="0 0 32 32">
      <path d="M2 7h10l3 3h15v17H2z" fill="currentColor"/>
    </symbol>
    <symbol id="icon-folder-open" viewBox="0 0 32 32">
      <path d="M2 6h10l3 3h13v4H7L2 27z" fill="currentColor" opacity=".75"/>
      <path d="M7 13h24l-5 14H2z" fill="currentColor"/>
    </symbol>
  </defs>
</svg>

<main class="stage">

  <!-- inactive state -->
  <section class="screen screen--inactive">
    <div class="state-tab">when inactive</div>
    <header class="app-bar"><span class="home-btn">Home</span><h1 class="app-title">Search</h1></header>
    <nav class="categories">
      <div class="category"><div class="category__icon"><svg><use href="#icon-folder"/></svg></div><div class="category__label">PORTFOLIO</div></div>
      <div class="category"><div class="category__icon"><svg><use href="#icon-house"/></svg></div><div class="category__label">PROPERTY</div></div>
      <div class="category"><div class="category__icon"><span class="person" role="img" aria-label="owner person icon"></span></div><div class="category__label">OWNER</div></div>
      <div class="category"><div class="category__icon"><span class="person" role="img" aria-label="tenant person icon"></span></div><div class="category__label">TENANT</div></div>
      <div class="category"><div class="category__icon"><span class="person" role="img" aria-label="staff man icon"></span><span class="person person--small" role="img" aria-label="staff woman icon"></span></div><div class="category__label">STAFF</div></div>
    </nav>
    <div class="search-band"><div class="search-field"></div></div>
    <ul class="results">
      <li class="result"><div class="result__icon"><svg><use href="#icon-house"/></svg></div><div class="result__card">24/9 Harbour Lane<br>CORVALE EAST NSW 2099</div></li>
      <li class="result"><div class="result__icon"><svg><use href="#icon-house"/></svg></div><div class="result__card">24/9 Harbour Lane<br>CORVALE EAST NSW 2099</div></li>
      <li class="result result--person"><div class="result__icon"><span class="person" role="img" aria-label="person icon"></span></div><div class="result__card">24/9 Harbour Lane<br>CORVALE EAST NSW 2099</div></li>
      <li class="result result--person"><div class="result__icon"><span class="person" role="img" aria-label="person icon"></span></div><div class="result__card">24/9 Harbour Lane<br>CORVALE EAST NSW 2099</div></li>
    </ul>
  </section>

  <!-- active state -->
  <section class="screen screen--active">
    <div class="state-tab">when active</div>
    <header class="app-bar"><span class="home-btn">Home</span><h1 class="app-title">Search</h1></header>
    <nav class="categories">
      <div class="category is-on"><div class="category__icon"><svg><use href="#icon-folder"/></svg></div><div class="category__label">PORTFOLIO</div></div>
      <div class="category is-on"><div class="category__icon"><svg><use href="#icon-house"/></svg></div><div class="category__label">PROPERTY</div></div>
      <div class="category is-on"><div class="category__icon"><span class="person" role="img" aria-label="owner person icon"></span></div><div class="category__label">OWNER</div></div>
      <div class="category is-on"><div class="category__icon"><span class="person" role="img" aria-label="tenant person icon"></span></div><div class="category__label">TENANT</div></div>
      <div class="category is-on"><div class="category__icon"><span class="person" role="img" aria-label="staff man icon"></span><span class="person person--small" role="img" aria-label="staff woman icon"></span></div><div class="category__label">STAFF</div></div>
    </nav>
    <div class="search-band"><div class="search-field"></div></div>
    <ul class="results">
      <li class="result"><div class="result__icon"><svg><use href="#icon-house"/></svg></div><div class="result__card">24/9 Harbour Lane<br>CORVALE EAST NSW 2099</div></li>
      <li class="result"><div class="result__icon"><svg><use href="#icon-house"/></svg></div><div class="result__card">24/9 Harbour Lane<br>CORVALE EAST NSW 2099</div></li>
      <li class="result result--person"><div class="result__icon"><span class="person" role="img" aria-label="person icon"></span></div><div class="result__card">24/9 Harbour Lane<br>CORVALE EAST NSW 2099</div></li>
      <li class="result result--person"><div class="result__icon"><span class="person" role="img" aria-label="person icon"></span></div><div class="result__card">24/9 Harbour Lane<br>CORVALE EAST NSW 2099</div></li>
    </ul>
  </section>

  <!-- single active state -->
  <section class="screen screen--single">
    <div class="state-tab">when active only one</div>
    <header class="app-bar"><span class="home-btn">Home</span><h1 class="app-title">Search</h1></header>
    <nav class="categories">
      <div class="category is-on"><div class="category__icon"><svg><use href="#icon-folder-open"/></svg></div><div class="category__label">ALL</div></div>
      <div class="category"><div class="category__icon"><svg><use href="#icon-house"/></svg></div><div class="category__label">PROPERTY</div></div>
      <div class="category"><div class="category__icon"><span class="person" role="img" aria-label="owner person icon"></span></div><div class="category__label">OWNER</div></div>
      <div class="category"><div class="category__icon"><span class="person" role="img" aria-label="tenant person icon"></span></div><div class="category__label">TENANT</div></div>
      <div class="category"><div class="category__icon"><span class="person" role="img" aria-label="staff man icon"></span><span class="person person--small" role="img" aria-label="staff woman icon"></span></div><div class="category__label">STAFF</div></div>
    </nav>
    <div class="search-band"><div class="search-field"></div></div>
    <ul class="results">
      <li class="result"><div class="result__icon"><svg><use href="#icon-house"/></svg></div><div class="result__card">24/9 Harbour Lane<br>CORVALE EAST NSW 2099</div></li>
      <li class="result"><div class="result__icon"><svg><use href="#icon-house"/></svg></div><div class="result__card">24/9 Harbour Lane<br>CORVALE EAST NSW 2099</div></li>
      <li class="result result--person"><div class="result__icon"><span class="person" role="img" aria-label="person icon"></span></div><div class="result__card">24/9 Harbour Lane<br>CORVALE EAST NSW 2099</div></li>
      <li class="result result--person"><div class="result__icon"><span class="person" role="img" aria-label="person icon"></span></div><div class="result__card">24/9 Harbour Lane<br>CORVALE EAST NSW 2099</div></li>
    </ul>
  </section>

  <div class="footer-band"></div>
</main>
</body>
</html>
```